SaaS Early tech startup business card design

Unique design for experience ecommerce platform company. the business cards will be used by executive members. conformance with color code is required.

```html
<!DOCTYPE html>
<html lang="en">
<head>
<meta charset="utf-8">
<title>Velto Business Card</title>
<link href="https://fonts.googleapis.com/css2?family=Roboto:wght@300;400;700&display=swap" rel="stylesheet">
<style>
  :root {
    --backdrop: #6b6868;
    --navy: #20203a;
    --teal-top: #05a394;
    --teal-bottom: #0f5d86;
    --teal-band: #0b6a78;
    --accent: #17a096;
    --ink-light: #f2f2f6;
    --mark-grey: #8d8d95;
  }
  * { margin: 0; padding: 0; box-sizing: border-box; }
  html, body { width: 1200px; height: 1200px; overflow: hidden; }
  body {
    background: var(--backdrop);
    font-family: "Roboto", sans-serif;
    position: relative;
  }
  .card {
    position: absolute;
    background: var(--navy);
    border-radius: 20px;
    overflow: hidden;
  }
  .card-front { left: 300px; top: 198px; width: 592px; height: 350px; }
  .card-back  { left: 292px; top: 637px; width: 594px; height: 347px; }

  .front-wordmark {
    position: absolute;
    left: 0; right: 0; top: 78px;
    text-align: center;
    font-weight: 700;
    font-size: 150px;
    line-height: 1;
    letter-spacing: -2px;
    color: var(--mark-grey);
  }
  .front-tagline {
    position: absolute;
    left: 0; right: 0; top: 246px;
    text-align: center;
    font-weight: 400;
    font-size: 18px;
    letter-spacing: 0.42em;
    padding-left: 0.42em;
    color: var(--ink-light);
  }

  .back-panel { position: absolute; left: 0; top: 0; }
  .back-wordmark {
    position: absolute;
    left: 40px; top: 105px;
    font-weight: 700;
    font-size: 98px;
    line-height: 1;
    letter-spacing: -1px;
    color: var(--ink-light);
  }
  .back-tagline {
    position: absolute;
    left: 44px; top: 203px;
    font-size: 14px;
    letter-spacing: 0.38em;
    color: var(--ink-light);
  }
  .contact-block {
    position: absolute;
    left: 360px; top: 78px;
    color: var(--ink-light);
  }
  .contact-name {
    font-weight: 700;
    font-size: 24px;
    color: var(--accent);
    letter-spacing: -0.3px;
    line-height: 1.2;
  }
  .contact-role { font-size: 15px; margin-top: 2px; }
  .contact-list { list-style: none; margin-top: 26px; }
  .contact-list li {
    display: flex; align-items: center;
    font-size: 15.5px; height: 22.5px;
  }
  .contact-list svg { width: 14px; height: 14px; margin-right: 16px; fill: var(--accent); }
  .contact-address { margin-top: 9px; font-size: 15.5px; line-height: 22.5px; }
</style>
</head>
<body>
  <section class="card card-front">
    <div class="front-wordmark">velto</div>
    <div class="front-tagline">MADE FOR MOTION</div>
  </section>

  <section class="card card-back">
    <svg class="back-panel" width="594" height="347" viewBox="0 0 594 347">
      <defs>
        <linearGradient id="tealGradient" x1="0" y1="0" x2="0.3" y2="1">
          <stop offset="0" stop-color="var(--teal-top)"/>
          <stop offset="1" stop-color="var(--teal-bottom)"/>
        </linearGradient>
      </defs>
      <circle cx="-16" cy="174" r="342" fill="var(--teal-band)"/>
      <circle cx="-16" cy="174" r="328" fill="url(#tealGradient)"/>
    </svg>
    <div class="back-wordmark">velto</div>
    <div class="back-tagline">MADE FOR MOTION</div>

    <div class="contact-block">
      <div class="contact-name">Rami K.</div>
      <div class="contact-role">CTO/Owner</div>
      <ul class="contact-list">
        <li><svg viewBox="0 0 16 16"><path d="M2 6c0-2 3-3 6-3s6 1 6 3v1h-3V6H5v1H2z M4 8h8l1 5H3z"/></svg>(00) 0111 VELTO</li>
        <li><svg viewBox="0 0 16 16"><path d="M1 3h14v10H1z M2.5 4.5 8 9l5.5-4.5z" fill-rule="evenodd"/></svg>info@velto.net</li>
        <li><svg viewBox="0 0 16 16"><path d="M8 1a7 7 0 1 0 0 14A7 7 0 0 0 8 1zm0 1.5c.8 1 1.4 2.6 1.5 4.5h-3C6.6 5.1 7.2 3.5 8 2.5zM2.6 7a5.5 5.5 0 0 1 3-4.2C5.2 4 5 5.4 5 7zm0 2H5c0 1.6.2 3 .7 4.2A5.5 5.5 0 0 1 2.6 9zm3.9 0h3c-.1 1.9-.7 3.5-1.5 4.5-.8-1-1.4-2.6-1.5-4.5zm4.5 0h2.4a5.5 5.5 0 0 1-3 4.2c.4-1.2.6-2.6.6-4.2zm0-2c0-1.6-.2-3-.7-4.2A5.5 5.5 0 0 1 13.4 7z"/></svg>www.velto.net</li>
      </ul>
      <div class="contact-address">Meridian Tower, Dubai<br>Harbor Tech District, UAE</div>
    </div>
  </section>
</body>
</html>
```